Granite Hollow Roofing & Exteriors Ltd

I would like to start a Facebook page for business that outlines granite hollow roofing . We have been in business since 2005 & have completed more than 5000 projects . Our company is area licensed, insured , covered by qlr , mzc member , journey man roofers , offer financing, zero down payment required , free quotes , serving red deer & area .

Please do not put years on the homepage.

Target Market(s)

Roofers in red deer & central Alberta

Industry/Entity Type

Roofing

Requirements
Must have
• Shingles , soffit , fascia , siding , gutters , roof repair , exterior painting , exterior washing .

```html
<!DOCTYPE html>
<html lang="en">
<head>
<meta charset="utf-8">
<title>Granite Hollow Roofing &amp; Exteriors – Cover</title>
<link href="https://fonts.googleapis.com/css2?family=Poppins:wght@400;500;700;800&display=swap" rel="stylesheet">
<style>
  :root {
    --brand-red: #b11f2a;
    --ink: #1d1d1f;
    --slate: #3d4a5c;
    --pale-grey: #e8e9eb;
    --paper: #ffffff;
    --badge-blue: #1f5f86;
  }
  * { margin: 0; padding: 0; box-sizing: border-box; }
  html, body { width: 1200px; height: 457px; overflow: hidden; background: var(--paper); }
  .cover {
    position: relative;
    width: 1200px; height: 457px;
    overflow: hidden;
    background: var(--paper);
    font-family: "Poppins", sans-serif;
    color: var(--ink);
  }
  .gallery { position: absolute; inset: 0; }

  .brand {
    position: absolute; left: 100px; top: 58px;
    display: flex; align-items: flex-start; gap: 10px;
  }
  .brand-mark { width: 12px; height: 12px; background: var(--brand-red); margin-top: 5px; }
  .brand-name {
    font-weight: 500; font-size: 17px; line-height: 19px;
    color: var(--slate); text-transform: uppercase;
  }

  .pitch { position: absolute; left: 76px; top: 140px; }
  .pitch-lead { font-size: 23px; font-weight: 500; line-height: 28px; letter-spacing: 0.2px; }
  .pitch-title {
    font-size: 36px; font-weight: 800; line-height: 32px;
    color: var(--brand-red); text-transform: uppercase; margin-top: 2px;
  }
  .pitch-services {
    font-size: 15.5px; font-weight: 500; line-height: 18px;
    text-transform: uppercase; margin-top: 8px;
  }

  .quote { position: absolute; left: 75px; top: 344px; display: flex; align-items: center; gap: 8px; }
  .quote-icon { width: 47px; height: 47px; }
  .quote-label { font-size: 16px; font-weight: 500; line-height: 18px; }
  .quote-phone { font-size: 23px; font-weight: 800; line-height: 28px; letter-spacing: 0.3px; }

  .licence { position: absolute; left: 373px; top: 344px; }
  .licence-label { font-size: 16px; font-weight: 500; line-height: 18px; }
  .licence-badges { display: flex; gap: 14px; margin-top: 8px; align-items: center; }
  .badge-board { width: 82px; height: 16px; background: var(--badge-blue); border-radius: 3px; }
  .badge-accredited { width: 50px; height: 19px; background: var(--badge-blue); border-radius: 3px; }
</style>
</head>
<body>
<main class="cover">
  <svg class="gallery" width="1200" height="457" viewBox="0 0 1200 457" aria-hidden="false">
    <defs>
      <linearGradient id="sidingGrad" x1="0" y1="0" x2="1" y2="1">
        <stop offset="0" stop-color="#7c8796"/><stop offset="0.6" stop-color="#4f7fb8"/><stop offset="1" stop-color="#3b5b2f"/>
      </linearGradient>
      <linearGradient id="garageGrad" x1="0" y1="0" x2="0" y2="1">
        <stop offset="0" stop-color="#9cb7d4"/><stop offset="0.45" stop-color="#687482"/><stop offset="1" stop-color="#5a5443"/>
      </linearGradient>
      <linearGradient id="shakeGrad" x1="0" y1="0" x2="0" y2="1">
        <stop offset="0" stop-color="#7a5a44"/><stop offset="0.5" stop-color="#3b3f47"/><stop offset="1" stop-color="#c9d0d6"/>
      </linearGradient>
      <linearGradient id="roofWorkGrad" x1="0" y1="0" x2="1" y2="1">
        <stop offset="0" stop-color="#d9dde2"/><stop offset="0.5" stop-color="#d9772c"/><stop offset="1" stop-color="#3a2f33"/>
      </linearGradient>
      <linearGradient id="buildGrad" x1="0" y1="0" x2="0" y2="1">
        <stop offset="0" stop-color="#2f6fd6"/><stop offset="0.45" stop-color="#7a5a3c"/><stop offset="1" stop-color="#b7a58c"/>
      </linearGradient>
    </defs>

    <polygon points="508,0 666,0 587,42" fill="var(--pale-grey)"/>
    <polygon points="755,0 913,0 834,40" fill="var(--brand-red)"/>
    <polygon points="1010,0 1165,0 1086,40" fill="var(--pale-grey)"/>
    <polygon points="1160,0 1200,0 1200,20" fill="#111"/>
    <polygon points="843,457 1067,457 960,400" fill="var(--brand-red)"/>
    <polygon points="1110,457 1200,457 1200,405" fill="var(--pale-grey)"/>

    <g role="img" aria-label="Photo: grey siding installed on a house with scaffolding brackets">
      <polygon points="717,0 833.5,60 833.5,180 717,240 600.5,180 600.5,60" fill="url(#sidingGrad)"/>
    </g>
    <g role="img" aria-label="Photo: finished garage with new shingles and grey siding">
      <polygon points="962,0 1078.5,60 1078.5,180 962,240 845.5,180 845.5,60" fill="url(#garageGrad)"/>
    </g>
    <g role="img" aria-label="Photo: vinyl shake, fascia and siding on a garage front">
      <polygon points="1208,0 1324.5,60 1324.5,180 1208,240 1091.5,180 1091.5,60" fill="url(#shakeGrad)"/>
    </g>
    <g role="img" aria-label="Photo: roofer in hard hat fastening metal roof panels">
      <polygon points="838,197.5 947,259 947,383 838,444.5 729,383 729,259" fill="url(#roofWorkGrad)"/>
    </g>
    <g role="img" aria-label="Photo: new home under construction with roof underlay">
      <polygon points="1076,197.5 1185,259 1185,383 1076,444.5 967,383 967,259" fill="url(#buildGrad)"/>
    </g>
  </svg>

  <div class="brand">
    <span class="brand-mark"></span>
    <p class="brand-name">Granite Hollow<br>Roofing<br>&amp; Exteriors</p>
  </div>

  <section class="pitch">
    <p class="pitch-lead">WE SPECIALIZE IN</p>
    <h1 class="pitch-title">Residential,<br>Commercial and<br>Industrial Roofing</h1>
    <p class="pitch-services">Shingles, Sofit, Fascia, Siding, Gutters, Roof Repair,<br>Exterior Painting, Exterior Washing and more...</p>
  </section>

  <div class="quote">
    <svg class="quote-icon" viewBox="0 0 48 48" aria-hidden="true">
      <circle cx="24" cy="24" r="24" fill="var(--brand-red)"/>
      <path d="M16 13c2-1 3 0 4 2l2 4c1 2 0 3-1 4l-1 1c1 3 4 6 7 7l1-1c1-1 2-2 4-1l4 2c2 1 3 2 2 4l-1 2c-1 2-3 2-6 1-7-3-13-9-16-16-1-3-1-5 1-6z" fill="#fff"/>
      <path d="M27 13a9 9 0 0 1 8 8M27 9a13 13 0 0 1 12 12" stroke="#fff" stroke-width="2.2" fill="none" stroke-linecap="round"/>
    </svg>
    <div>
      <p class="quote-label">CALL FOR A FREE QUOTE</p>
      <p class="quote-phone">403-555-0187</p>
    </div>
  </div>

  <div class="licence">
    <p class="licence-label">LISCENCED BY</p>
    <div class="licence-badges">
      <span class="badge-board"></span>
      <span class="badge-accredited"></span>
    </div>
  </div>
</main>
</body>
</html>
```